Laboratory and geotechnical service provider needs Word template

We require a new Word Template for our business. We are looking for a modern, business-like format. We typically generate reports such as management plans, business plans, method statements, technical reports. These reports cover generally between 5 and 30 pages, but sometimes up to 500 pages including the appendices.

Lab reports have their own formats and are not parts of this scope.

Target Market(s)

We report to Clients such as construction industry contractors, governmental departments and engineering consultants.

Industry/Entity Type

Technical Service

Colors

Designer to choose colors to be used in the design.

Requirements
Must have
• The report needs a fancy cover page with a title field, subtitle, project field, client name field, reference number field. Photo/graphics as background on cover. Second page needs a revision table for document control. Table of contents up to 2 levels. Appendices to be part of TOC. Report first page with custom headings for body text, titles, subtitles, headings 1, 2, 3, etc. Include a table with caption, figure with caption, bullet list, numbered list. Appendix page. Please use fonts consistently, choose a common, but professional, modern font.
Nice to have
• We traditionally use black and yellow as company colours. Please visit our company page www.brennixtesting.com.
Should not have
• The two attached word documents is what we use now for your information, we are looking for something better!

```html
<!DOCTYPE html>
<html lang="en">
<head>
<meta charset="utf-8">
<title>Brennix Testing – Report Template</title>
<link href="https://fonts.googleapis.com/css2?family=Source+Sans+3:wght@300;400;600;700&display=swap" rel="stylesheet">
<style>
:root{
  --yellow:#f9dc00;
  --yellow-soft:#fff3a6;
  --black:#231f20;
  --ink:#2b2b2b;
  --grey-bg:#e8e8e8;
  --white:#ffffff;
  --watermark:#f0f0f0;
}
*{margin:0;padding:0;box-sizing:border-box}
html,body{width:859px;height:1200px;overflow:hidden}
body{background:var(--grey-bg);font-family:"Source Sans 3",Arial,sans-serif;color:var(--ink);position:relative}
.page{position:absolute;width:268px;height:379px;background:var(--white);overflow:hidden}
.col1{left:13px}.col2{left:295px}.col3{left:577px}
.row1{top:16px}.row2{top:411px}.row3{top:807px}

/* inner page furniture */
.edge{position:absolute;left:3px;top:0;width:4px;height:379px;background:linear-gradient(var(--yellow) 0 56%,var(--black) 56% 100%)}
.brand{position:absolute;right:8px;top:14px;white-space:nowrap;font-weight:700;font-size:6px;line-height:7px;color:var(--black)}
.bar{position:absolute;left:11px;right:7px;height:5px;background:var(--yellow);font-size:4.6px;line-height:5px;text-align:center;color:var(--black);text-transform:uppercase}
.bar.dark{background:var(--black);color:var(--white)}
.bar.num{text-align:left;padding-left:16px}
.rule{position:absolute;left:6px;right:14px;bottom:5px;height:1px;background:var(--black)}
.folio{position:absolute;right:5px;bottom:3px;font-size:4.5px;font-weight:700;color:var(--black)}
.body{position:absolute;left:15px;right:10px;font-size:4.3px;line-height:5.4px;font-weight:400;color:var(--ink)}
.body p{margin-bottom:3.6px;text-align:justify}
.body ul{list-style:none;margin:3px 0 4px 6px}
.body li::before{content:"•";margin-right:3px}
.chapter{font-size:5px;font-weight:600;color:var(--black);border-bottom:.5px solid var(--black);display:inline-block;margin-bottom:4px}

/* cover */
.cover{background:var(--yellow)}
.cover svg{position:absolute;inset:0}
.cover-brand{position:absolute;left:14px;top:40px;white-space:nowrap;font-weight:700;font-size:12px;line-height:14px;color:var(--black)}
.cover-text{position:absolute;right:10px;text-align:right;color:var(--white)}
.cover-title{top:60px;font-size:17.5px;line-height:20px;font-weight:600;letter-spacing:.2px}
.cover-line{position:absolute;right:10px;top:113px;width:41px;height:1.2px;background:var(--white)}
.cover-sub{font-weight:700;font-size:6.6px;line-height:8px}
.cover-copy{font-size:6px;line-height:7.6px;font-weight:400}
.cover-url{position:absolute;left:5px;bottom:6px;font-size:3.8px;letter-spacing:2.2px;font-weight:700;color:var(--black)}

/* revision table */
.rev{position:absolute;left:18px;top:80px;width:235px;border-collapse:collapse;font-size:4.3px;font-weight:400;text-align:center}
.rev th{background:var(--yellow);font-weight:400;height:8px}
.rev td{height:8.4px;border-right:.4px solid #fff}
.rev tr.tint td{background:var(--yellow-soft)}
.box{display:inline-block;width:4px;height:4px;border:.5px solid var(--black);vertical-align:middle;margin-left:2px}
.box.on{background:var(--black);box-shadow:inset 0 0 0 .6px #fff}
.watermark{position:absolute;left:10px;right:10px;top:230px;text-align:center;white-space:nowrap;font-weight:700;font-size:26px;line-height:30px;color:var(--watermark)}
.fine{position:absolute;left:10px;right:12px;top:359px;font-size:2.6px;line-height:3.2px;font-style:italic;color:#555}

/* toc */
.toc{position:absolute;left:15px;right:10px;top:68px;font-size:4.5px;line-height:9.45px;font-weight:400;color:var(--ink);text-transform:uppercase}
.toc div{display:flex}
.toc .l2{padding-left:13px}.toc .l3{padding-left:23px;text-transform:none}
.toc .lead{flex:1;border-bottom:.5px dotted #777;margin:0 1.5px 2.6px}

/* chart */
.chart{position:absolute;left:55px;top:64px}
.donut{position:absolute;left:45px;top:276px}
.pct{position:absolute;font-size:10px;font-weight:600;color:var(--black)}
.divider{position:absolute;left:161px;top:268px;width:.8px;height:93px;background:var(--black)}
.aside{position:absolute;left:172px;top:276px;width:86px;font-size:4.3px;line-height:9.4px}

/* figure with description */
.photo{position:absolute;background:linear-gradient(160deg,#cfcfcf,#7b7b7b 60%,#9d9d9d)}
.vline{position:absolute;width:1px;background:var(--yellow)}
.stat{position:absolute;left:143px;font-size:16px;font-weight:300;color:var(--black)}
.stat small{font-size:4.5px;margin-left:3px;vertical-align:middle}

/* numbered list */
.numbered{position:absolute;left:15px;right:10px;top:60px;font-size:4.3px;line-height:5.4px;list-style:none;counter-reset:n}
.numbered li{counter-increment:n;position:relative;padding-left:10px;height:19.6px}
.numbered li::before{content:counter(n) ".";position:absolute;left:0}
</style>
</head>
<body>

<!-- Cover -->
<section class="page cover col1 row1">
  <svg width="268" height="379" viewBox="0 0 268 379">
    <path d="M148 0H268V379H0V150C70 150 122 105 148 0Z" fill="#231f20"/>
    <defs>
      <linearGradient id="labPhoto" x1="0" y1="0" x2="1" y2="1">
        <stop offset="0" stop-color="#cfcfc8"/><stop offset=".55" stop-color="#8f8c80"/><stop offset="1" stop-color="#c9b24a"/>
      </linearGradient>
      <linearGradient id="sitePhoto" x1="0" y1="0" x2="0" y2="1">
        <stop offset="0" stop-color="#e6e6e6"/><stop offset="1" stop-color="#6f6f6f"/>
      </linearGradient>
    </defs>
    <path role="img" aria-label="Photo of a technician handling sample trays in a laboratory store room" d="M0 158C72 158 126 175 138 245C146 300 118 345 70 368H0Z" fill="url(#labPhoto)"/>
    <path d="M0 368H70C95 357 112 347 124 335C118 360 100 379 85 379H0Z" fill="#f9dc00"/>
    <circle role="img" aria-label="Photo of a drilling rig on a construction site" cx="176" cy="329" r="36" fill="url(#sitePhoto)"/>
    <circle role="img" aria-label="Photo of laboratory testing equipment" cx="238" cy="364" r="25" fill="url(#sitePhoto)"/>
  </svg>
  <div class="cover-brand">BRENNIX TESTING</div>
  <div class="cover-text cover-title">YOUR HEADING<br>GOES HERE</div>
  <div class="cover-line"></div>
  <div class="cover-text cover-sub" style="top:124px">Subtitle goes here</div>
  <div class="cover-text" style="top:160px"><div class="cover-sub">Project goes here</div><div class="cover-copy">Lorem ipsum dolor sit amet, consectetuer<br>adipiscing elit, sed diam nonummy nibh<br>euismod tincidunt</div></div>
  <div class="cover-text" style="top:210px"><div class="cover-sub">Client name goes here</div><div class="cover-copy">Lorem ipsum dolor sit amet, consec-<br>tetuer adipiscing elit, sed diam<br>nonummy</div></div>
  <div class="cover-text cover-sub" style="top:264px">Reference number goes here</div>
  <div class="cover-url">WWW.BRENNIXTESTING.COM</div>
</section>

<!-- Revision table -->
<section class="page col2 row1">
  <div class="edge"></div>
  <div class="brand">BRENNIX TESTING</div>
  <div class="bar" style="top:42px">Revision Table</div>
  <div class="watermark">BRENNIX TESTING</div>
  <table class="rev">
    <tr><th>REV</th><th>DATE</th><th>DETAILS</th><th>CHECKED</th><th>APPROVED</th></tr>
    <tr><td></td><td></td><td></td><td>QA Dept. Mgr</td><td>General Manager</td></tr>
    <tr class="tint"><td></td><td></td><td></td><td></td><td></td></tr>
    <tr><td>1</td><td>10-Nov-19</td><td>Draft plan</td><td>RTM</td><td>LDH</td></tr>
    <tr class="tint"><td>2</td><td></td><td></td><td></td><td></td></tr>
    <tr><td></td><td></td><td></td><td style="font-size:3.3px">COPY NO.</td><td></td></tr>
    <tr class="tint"><td></td><td></td><td></td><td style="font-size:3.3px">CONTROLLED COPY</td><td>YES<span class="box"></span>&nbsp;&nbsp;&nbsp; NO<span class="box on"></span></td></tr>
  </table>
  <div class="fine">Lorem ipsum dolor sit amet, consectetuer adipiscing elit, sed diam nonummy nibh euismod tincidunt ut laoreet dolore magna aliquam erat volutpat. Ut wisi enim ad minim veniam, quis nostrud exerci tation ullamcorper suscipit.</div>
  <div class="rule"></div><div class="folio">2</div>
</section>

<!-- Table of contents -->
<section class="page col3 row1">
  <div class="edge"></div>
  <div class="brand">BRENNIX TESTING</div>
  <div class="bar" style="top:42px">Table of Contents</div>
  <nav class="toc">
    <div>1. Introduction<span class="lead"></span>2</div>
    <div>2. Project Overview<span class="lead"></span>2</div>
    <div class="l2">2.1. Company Overview<span class="lead"></span>2</div>
    <div class="l2">2.2. LIMS Overview<span class="lead"></span>3</div>
    <div class="l2">2.3. Hardware and Operating System Overview<span class="lead"></span>3</div>
    <div class="l3">2.3.1 Direct links to instruments/systems<span class="lead"></span>3</div>
    <div class="l3">2.3.2 Interfaces with other software<span class="lead"></span>4</div>
    <div class="l2">2.4. Database Overview<span class="lead"></span>4</div>
    <div>3. LIMS Technical Requirements<span class="lead"></span>5</div>
    <div class="l2">3.1. Sample Registration<span class="lead"></span>5</div>
    <div class="l2">3.2. Labelling<span class="lead"></span>6</div>
    <div class="l2">3.3. Test Program (TP)<span class="lead"></span>7</div>
    <div class="l2">3.4. Electronic Worksheets and Calculations<span class="lead"></span>8</div>
    <div class="l2">3.5. Workflows<span class="lead"></span>9</div>
    <div class="l2">3.6. Acquiring Analytical Results<span class="lead"></span>10</div>
    <div class="l2">3.7. Sample Tracking<span class="lead"></span>11</div>
    <div class="l2">3.8. Data Validation and Approval<span class="lead"></span>11</div>
    <div class="l2">3.9. Technical Reporting<span class="lead"></span>12</div>
    <div class="l2">3.10. Data Management<span class="lead"></span>13</div>
    <div class="l2">3.11. Number of Concurrent Users<span class="lead"></span>13</div>
    <div class="l2">3.12. Security<span class="lead"></span>14</div>
    <div class="l2">3.13. Tables of Reference Information<span class="lead"></span>15</div>
    <div>4. LIMS Business Management Requirements<span class="lead"></span>16</div>
    <div class="l2">4.1. Management Access<span class="lead"></span>16</div>
    <div class="l2">4.2. Client Access<span class="lead"></span>17</div>
    <div class="l2">4.3. Business Reporting<span class="lead"></span>17</div>
    <div>Appendix A Laboratories Process Flow<span class="lead"></span>18</div>
    <div>Appendix B Instrument List with Network Connectivity<span class="lead"></span>19</div>
    <div>Appendix C List of Tests<span class="lead"></span>20</div>
  </nav>
  <div class="rule"></div><div class="folio">3</div>
</section>

<!-- Introduction -->
<section class="page col1 row2">
  <div class="edge"></div>
  <div class="brand">BRENNIX TESTING</div>
  <div class="bar num" style="top:42px">1 &nbsp;|&nbsp; Introduction</div>
  <div class="body" style="top:68px">
    <p>The purpose of this Stakeholder Management Plan is to define the requirements, processes, and techniques for engaging stakeholders based on an analysis of their needs, interests, and abilities to impact the project.</p>
    <p>The objectives of the Stakeholder Management Plan are to document and communicate how information will be disseminated to, and received from all stakeholders connected with the project.<br>The SMP shall therefore:</p>
    <ul><li>Identify who the stakeholders are</li><li>Establish the requirements of each stakeholder</li><li>The requirements of the project to receive information and/or obtain approvals from stakeholders</li><li>Analyse the power and interest of each stakeholder</li><li>Define the means and frequency of communication with each stakeholder</li></ul>
  </div>
  <div class="bar num" style="top:187px">2 &nbsp;|&nbsp; Identifying Stakeholders</div>
  <div class="body" style="top:210px">
    <p>As part of the project planning process, the project management team shall identity potential stakeholders against the following criteria:</p>
    <ul><li>Will the person or their organization be directly or indirectly affected by this project?</li><li>Does the person or their organization hold a position from which they can influence the project?</li><li>Does the person have an impact on the project's resources (material, personnel, funding)?</li><li>Does the person or their organization have any special skills or capabilities the project will require?</li><li>Does the person potentially benefit from the project or are they in a position to resist this change?</li></ul>
    <p>Stakeholders may include BOTH internal and external personnel or organisations.</p>
    <p><b>Internal stakeholders</b> might include the project team, including contractors and vendors, as well as top management, resourcing directors, accounting department members, and others who want to see the project run efficiently and profitably.</p>
    <p><b>External stakeholders</b> are individuals or groups outside the organization who could be impacted by the project or those who govern policy that influences and could affect the project. Besides identifying and classifying all stakeholders, it is important to include everyone who will be even tangentially impacted by the project.</p>
    <p>Once identified, all Stakeholders shall be recorded in the Stakeholder Management Register.<br><i>(See Appendix A)</i></p>
  </div>
  <div class="rule"></div><div class="folio">4</div>
</section>

<!-- Figures / charts -->
<section class="page col2 row2">
  <div class="edge"></div>
  <div class="brand">BRENNIX TESTING</div>
  <div class="bar num" style="top:42px">5 &nbsp;|&nbsp; Figure with Caption / Charts</div>
  <svg class="chart" width="160" height="96" viewBox="0 0 160 96">
    <g stroke="#dcdcdc" stroke-width=".5">
      <line x1="0" y1="2" x2="160" y2="2"/><line x1="0" y1="10" x2="160" y2="10"/><line x1="0" y1="18" x2="160" y2="18"/><line x1="0" y1="26" x2="160" y2="26"/><line x1="0" y1="34" x2="160" y2="34"/><line x1="0" y1="42" x2="160" y2="42"/><line x1="0" y1="50" x2="160" y2="50"/><line x1="0" y1="58" x2="160" y2="58"/><line x1="0" y1="66" x2="160" y2="66"/><line x1="0" y1="74" x2="160" y2="74"/><line x1="0" y1="82" x2="160" y2="82"/><line x1="0" y1="90" x2="160" y2="90"/>
    </g>
    <line x1="0" y1="0" x2="0" y2="94" stroke="#999" stroke-width=".5"/>
    <line x1="0" y1="94" x2="160" y2="94" stroke="#999" stroke-width=".5"/>
    <rect x="17" y="67" width="20" height="27" fill="#f9dc00"/>
    <rect x="43" y="54" width="20" height="40" fill="#231f20"/>
    <rect x="69" y="33" width="20" height="61" fill="#f9dc00"/>
    <rect x="95" y="47" width="20" height="47" fill="#231f20"/>
    <rect x="121" y="40" width="20" height="54" fill="#f9dc00"/>
  </svg>
  <div class="body" style="top:176px">
    <p>The purpose of this Stakeholder Management Plan is to define the requirements, processes, and techniques for engaging stakeholders based on an analysis of their needs, interests, and abilities to impact the project.</p>
    <p>The objectives of the Stakeholder Management Plan are to document and communicate how information will be disseminated to, and received from all stakeholders connected with the project.<br>The SMP shall therefore:</p>
    <ul><li>Identify who the stakeholders are</li><li>Establish the requirements of each stakeholder</li><li>The requirements of the project to receive information and/or obtain approvals from stakeholders</li><li>Analyse the power and interest of each stakeholder</li><li>Define the means and frequency of communication with each stakeholder</li></ul>
  </div>
  <svg class="donut" width="80" height="80" viewBox="0 0 80 80">
    <circle cx="40" cy="40" r="31" fill="none" stroke="#f9dc00" stroke-width="11"/>
    <path d="M40 9A31 31 0 0 1 71 40" fill="none" stroke="#231f20" stroke-width="11" transform="rotate(20 40 40)"/>
  </svg>
  <div class="pct" style="left:123px;top:281px">25%</div>
  <div class="pct" style="left:30px;top:339px">75%</div>
  <div class="divider"></div>
  <div class="aside">Lorem ipsum dolor sit amet, consec-<br>tetuer adipiscing elit, sed diam<br>nonummy nibh euismod tincidunt ut<br>laoreet dolore magna aliquam erat<br>volutpat. Ut wisi enim ad minim<br>veniam, quis nostrud exerci tation<br>ullamcorper suscipit lobortis nisl ut</div>
  <div class="rule"></div><div class="folio">10</div>
</section>

<!-- Chapters -->
<section class="page col3 row2">
  <div class="edge"></div>
  <div class="brand">BRENNIX TESTING</div>
  <div class="bar" style="top:42px">Your Title Gose Here</div>
  <div class="body" style="top:60px">
    <div class="chapter">CHAPTER 1</div>
    <p>Lorem ipsum dolor sit amet, consectetuer adipiscing elit, sed diam nonummy nibh euismod tincidunt ut laoreet dolore magna aliquam erat volutpat. Ut wisi enim ad minim veniam, quis nostrud exerci tation ullamcorper suscipit lobortis nisl ut aliquip ex ea commodo consequat. Duis autem vel eum iriure dolor in hendrerit in vulputate velit esse molestie consequat, vel illum dolore eu feugiat nulla facilisis at vero eros et accumsan et iusto odio dignissim qui blandit praesent luptatum zzril delenit augue duis dolore te feugait nulla facilisi. Lorem ipsum dolor sit amet, cons ectetuer adipiscing elit, sed diam nonummy nibh euismod tincidunt ut laoreet dolore magna aliquam erat volutpat. Ut wisi enim ad minim veniam, quis nostrud exerci tation ullamcorper suscipit lobortis nisl ut aliquip ex ea commodo consequat.</p>
  </div>
  <div class="body" style="top:165px">
    <div class="chapter">CHAPTER 2</div>
    <p>Lorem ipsum dolor sit amet, consectetuer adipiscing elit, sed diam nonummy nibh euismod tincidunt ut laoreet dolore magna aliquam erat volutpat. Ut wisi enim ad minim veniam, quis nostrud exerci tation ullamcorper suscipit lobortis nisl ut aliquip ex ea commodo consequat. Duis autem vel eum iriure dolor in hendrerit in vulputate velit esse molestie consequat, vel illum dolore eu feugiat nulla facilisis at vero eros et accumsan et iusto odio dignissim qui blandit praesent luptatum zzril delenit augue duis dolore te feugait nulla facilisi. Lorem ipsum dolor sit amet, cons ectetuer adipiscing elit, sed diam nonummy nibh euismod tincidunt ut laoreet dolore magna aliquam erat volutpat. Ut wisi enim ad minim veniam, quis nostrud exerci tation ullamcorper suscipit lobortis nisl ut aliquip ex ea commodo consequat.</p>
  </div>
  <div class="body" style="top:270px">
    <div class="chapter">CHAPTER 3</div>
    <p>Lorem ipsum dolor sit amet, consectetuer adipiscing elit, sed diam nonummy nibh euismod tincidunt ut laoreet dolore magna aliquam erat volutpat. Ut wisi enim ad minim veniam, quis nostrud exerci tation ullamcorper suscipit lobortis nisl ut aliquip ex ea commodo consequat. Duis autem vel eum iriure dolor in hendrerit in vulputate velit esse molestie consequat, vel illum dolore eu feugiat nulla facilisis at vero eros et accumsan et iusto odio dignissim qui blandit praesent luptatum zzril delenit augue duis dolore te feugait nulla facilisi. Lorem ipsum dolor sit amet, cons ectetuer adipiscing elit, sed diam nonummy nibh euismod tincidunt ut laoreet dolore magna aliquam erat volutpat.</p>
  </div>
  <div class="rule"></div><div class="folio">14</div>
</section>

<!-- Paragraphs & figure -->
<section class="page col1 row3">
  <div class="edge"></div>
  <div class="brand">BRENNIX TESTING</div>
  <div class="bar" style="top:42px">Paragraph Examples</div>
  <div class="body" style="top:59px">
    <p style="text-indent:14px">Lorem ipsum dolor sit amet, consectetuer adipiscing elit, sed diam nonummy nibh euismod tincidunt ut laoreet dolore magna aliquam erat volutpat. Ut wisi enim ad minim veniam, quis nostrud exerci tation ullamcorper suscipit lobortis nisl ut aliquip ex ea commodo consequat. Duis autem vel eum iriure dolor in hendrerit in vulputate velit esse molestie consequat, vel illum dolore eu feugiat nulla facilisis at vero eros et accumsan et iusto odio dignissim qui blandit praesent luptatum zzril delenit augue duis dolore te feugait nulla facilisi.</p>
    <p style="text-indent:14px">Lorem ipsum dolor sit amet, cons ectetuer adipiscing elit, sed diam nonummy nibh euismod tincidunt ut laoreet dolore magna aliquam erat volutpat. Ut wisi enim ad minim veniam, quis nostrud exerci tation ullamcorper suscipit lobortis nisl ut aliquip ex ea commodo consequat.</p>
    <p style="text-indent:14px">Lorem ipsum dolor sit amet, cons ectetuer adipiscing elit, sed diam nonummy nibh euismod tincidunt ut laoreet dolore magna aliquam erat volutpat. Ut wisi enim ad minim veniam, quis nostrud exerci tation ullamcorper suscipit lobortis nisl ut aliquip ex ea commodo consequat. Duis autem vel eum iriure dolor in hendrerit in vulputate velit esse molestie consequat, vel illum dolore eu feugiat nulla facilisis at vero eros et accumsan et iusto odio dignissim qui blandit praesent luptatum zzril delenit augue duis dolore te feugait nulla facilisi. Lorem ipsum dolor sit amet, cons ectetuer adipiscing elit, sed diam nonummy nibh euismod tincidunt ut laoreet dolore magna aliquam erat volutpat.</p>
  </div>
  <div class="bar dark" style="top:199px">Figure with Description</div>
  <div class="photo" role="img" aria-label="Black and white photo of a drilling rig on a desert site" style="left:21px;top:222px;width:98px;height:132px"></div>
  <div class="vline" style="left:128px;top:222px;height:132px"></div>
  <div class="body" style="left:137px;right:25px;top:224px">
    <p style="text-indent:14px">Lorem ipsum dolor sit amet, consectetuer adipiscing elit, sed diam nonummy nibh euismod tincidunt ut laoreet dolore magna aliquam erat volutpat. Ut wisi enim ad minim veniam, quis nostrud exerci tation ullamcorper suscipit lobortis nisl ut aliquip ex ea commodo consequat. Duis autem vel eum iriure dolor in hendrerit in vulputate velit esse molestie consequat, vel illum dolore eu feugiat nulla facilisis at vero eros et accumsan et iusto odio dignissim qui blandit praesent luptatum zzril</p>
  </div>
  <div class="stat" style="top:310px">25%<small>Lorem ipsum</small></div>
  <div class="stat" style="top:338px">75%<small>Lorem ipsum</small></div>
  <div class="rule"></div><div class="folio">16</div>
</section>

<!-- Numbered list -->
<section class="page col2 row3">
  <div class="edge"></div>
  <div class="brand">BRENNIX TESTING</div>
  <div class="bar" style="top:42px">Numbered List</div>
  <ol class="numbered">
    <li>Lorem ipsum dolor sit amet, consectetuer adipiscing elit, sed diam nonummy nibh euismod tincidunt ut laoreet dolore magna aliquam erat volutpat.</li>
    <li>Ut wisi enim ad minim veniam, quis nostrud exerci tation ullamcorper suscipit lobortis nisl ut aliquip ex ea commodo consequat.</li>
    <li>Duis autem vel eum iriure dolor in hendrerit in vulputate velit esse molestie consequat, vel illum dolore eu feugiat nulla facilisis at vero eros et accumsan et iusto odio dignissim qui blandit praesent luptatum zzril delenit augue duis dolore te feugait nulla facilisi.</li>
    <li>Lorem ipsum dolor sit amet, cons ectetuer adipiscing elit, sed diam nonummy nibh euismod tincidunt ut laoreet dolore magna aliquam erat volutpat.</li>
    <li>Ut wisi enim ad minim veniam, quis nostrud exerci tation ullamcorper suscipit lobortis nisl ut aliquip ex ea commodo consequat.</li>
    <li>Lorem ipsum dolor sit amet, consectetuer adipiscing elit, sed diam nonummy nibh euismod tincidunt ut laoreet dolore magna aliquam erat volutpat.</li>
    <li>Ut wisi enim ad minim veniam, quis nostrud exerci tation ullamcorper suscipit lobortis nisl ut aliquip ex ea commodo consequat.</li>
    <li>Duis autem vel eum iriure dolor in hendrerit in vulputate velit esse molestie consequat, vel illum dolore eu feugiat nulla facilisis at vero eros et accumsan et iusto odio dignissim qui blandit praesent luptatum zzril delenit augue duis dolore te feugait nulla facilisi.</li>
    <li>lorem ipsum dolor sit amet, cons ectetuer adipiscing elit, sed diam nonummy nibh euismod tincidunt ut laoreet dolore magna aliquam erat volutpat.</li>
    <li>Ut wisi enim ad minim veniam, quis nostrud exerci tation ullamcorper suscipit lobortis nisl ut aliquip ex ea commodo consequat.</li>
  </ol>
  <div class="rule"></div><div class="folio">17</div>
</section>

<!-- Appendices -->
<section class="page col3 row3">
  <div class="edge"></div>
  <div class="brand">BRENNIX TESTING</div>
  <div class="bar dark" style="top:44px">Appendix A</div>
  <div class="body" style="top:58px;left:18px">
    <p>Lorem ipsum dolor sit amet, consectetuer adipiscing elit, sed diam nonummy nibh euismod tincidunt ut laoreet dolore magna aliquam erat volutpat. Ut wisi enim ad minim veniam, quis nostrud exerci tation ullamcorper suscipit lobortis nisl ut aliquip ex ea commodo consequat. Duis autem vel eum iriure dolor in hendrerit in vulputate velit esse molestie consequat, vel illum dolore eu feugiat nulla facilisis at vero eros et accumsan et iusto odio dignissim qui blandit praesent luptatum zzril delenit augue duis dolore te feugait nulla facilisi. Lorem ipsum dolor sit amet, cons ectetuer adipiscing elit, sed diam nonummy nibh euismod tincidunt ut laoreet dolore magna aliquam erat volutpat. Ut wisi enim ad minim veniam, quis nostrud exerci tation ullamcorper suscipit lobortis nisl ut aliquip ex ea commodo consequat.</p>
  </div>
  <div class="bar dark" style="top:153px">Appendix B</div>
  <div class="body" style="top:167px;left:18px">
    <p>Lorem ipsum dolor sit amet, consectetuer adipiscing elit, sed diam nonummy nibh euismod tincidunt ut laoreet dolore magna aliquam erat volutpat. Ut wisi enim ad minim veniam, quis nostrud exerci tation ullamcorper suscipit lobortis nisl ut aliquip ex ea commodo consequat. Duis autem vel eum iriure dolor in hendrerit in vulputate velit esse molestie consequat, vel illum dolore eu feugiat nulla facilisis at vero eros et accumsan et iusto odio dignissim qui blandit praesent luptatum zzril delenit augue duis dolore te feugait nulla facilisi. Lorem ipsum dolor sit amet, cons ectetuer adipiscing elit, sed diam nonummy nibh euismod tincidunt ut laoreet dolore magna aliquam erat volutpat. Ut wisi enim ad minim veniam, quis nostrud exerci tation ullamcorper suscipit lobortis nisl ut aliquip ex ea commodo consequat.</p>
  </div>
  <div class="bar dark" style="top:265px;left:9px;right:9px">Appendix C</div>
  <div class="body" style="top:279px;left:16px">
    <p>Lorem ipsum dolor sit amet, consectetuer adipiscing elit, sed diam nonummy nibh euismod tincidunt ut laoreet dolore magna aliquam erat volutpat. Ut wisi enim ad minim veniam, quis nostrud exerci tation ullamcorper suscipit lobortis nisl ut aliquip ex ea commodo consequat. Duis autem vel eum iriure dolor in hendrerit in vulputate velit esse molestie consequat, vel illum dolore eu feugiat nulla facilisis at vero eros et accumsan et iusto odio dignissim qui blandit praesent luptatum zzril delenit augue duis dolore te feugait nulla facilisi.</p>
    <p>Lorem ipsum dolor sit amet, cons ectetuer adipiscing elit, sed diam nonummy nibh euismod tincidunt ut laoreet dolore magna a</p>
  </div>
  <div class="rule"></div><div class="folio">20</div>
</section>

</body>
</html>
```